Law Firm in Texas in need of new letterhead

Law Firm in Fort Worth, TX, USA named "Pell & Varnum, Attorneys-At-Law, LLP." This is a general practice law firm that mostly does Family Law and Criminal Defense work.

We are looking for a new letterhead that has a "classical" appeal, with modern elements.

Any color combination is fine, but please note that we do fax many documents, so the design must be clearly legible in Black and White.

We would like our letterhead to project a sense of professionalism, integrity, and ability.

Target Market(s)

Letterhead will be for correspondence generally with other attorneys and clients.

Industry/Entity Type

Law Firm

Logo Text

Pell & Varnum, Attorneys-At-Law, LLP.

Logo styles of interest
Pictorial/Combination Logo
Wordmark Logo
Lettermark Logo
Requirements
Nice to have
• Although not necessary, a "Texas Star" that is incorporated into the design would be a nice touch.
Should not have
• Colors that do not convert to B&W easily

```html
<!DOCTYPE html>
<html lang="en">
<head>
<meta charset="utf-8">
<title>Pell &amp; Varnum Letterhead</title>
<link rel="stylesheet" href="https://fonts.googleapis.com/css2?family=Cinzel:wght@400&family=Questrial&display=swap">
<style>
  :root {
    --navy: #1d4a73;
    --backdrop: #ebebeb;
    --paper: #f7f7f7;
    --ink: #3a3a3a;
    --muted: #8a8f96;
    --rule: #b8c2cc;
    --watermark: #e4e4e4;
  }
  * { margin: 0; padding: 0; box-sizing: border-box; }
  html, body { width: 1200px; height: 815px; overflow: hidden; background: var(--backdrop); }
  .canvas { position: relative; width: 1200px; height: 815px; }
  .sheet { position: absolute; top: 72px; width: 482px; height: 680px; background: var(--paper); }
  .sheet--blank { left: 80px; }
  .sheet--letter { left: 638px; }
  .sheet__band { position: absolute; left: 0; right: 0; bottom: 0; height: 9px; background: var(--navy); }

  .wordmark { position: absolute; font-family: "Cinzel", serif; font-weight: 400; color: var(--navy); line-height: 1; text-align: center; }
  .wordmark__name { display: block; font-size: 22px; letter-spacing: 0.3px; }
  .wordmark__tagline { display: block; font-size: 11.5px; margin-top: 4px; letter-spacing: 0.2px; }
  .sheet--blank .wordmark { left: 146px; top: 38px; width: 190px; }
  .sheet--letter .wordmark { right: 32px; top: 44px; width: 196px; }

  .star-area { position: absolute; left: 120px; top: 340px; width: 242px; height: 230px;
    background: radial-gradient(circle at 50% 50%, var(--watermark) 0%, var(--watermark) 40%, var(--paper) 72%); }

  .letter-body { position: absolute; left: 35px; top: 188px; width: 418px; font-family: "Questrial", sans-serif; color: var(--ink); }
  .letter-body__salutation { font-size: 11px; font-weight: 700; color: #222; margin-bottom: 12px; }
  .letter-body p { font-size: 8.2px; line-height: 11.3px; text-align: justify; margin-bottom: 11px; }
  .closing { position: absolute; right: 30px; top: 507px; text-align: right; font-family: "Questrial", sans-serif; }
  .closing__phrase { font-size: 8px; color: var(--ink); }
  .closing__name { font-size: 11px; font-weight: 700; color: #222; margin-top: 9px; }
  .signature-area { position: absolute; left: 268px; top: 476px; width: 118px; height: 64px;
    background: radial-gradient(ellipse at 50% 50%, #dfe3ee 0%, var(--paper) 70%); }

  .footer { position: absolute; font-family: "Questrial", sans-serif; font-size: 5.6px; color: var(--muted); line-height: 1; }
  .footer strong { color: var(--navy); font-weight: 700; }
  .footer__address { white-space: nowrap; }
  .footer__rule { height: 1px; background: var(--rule); margin: 6px 0 5px; }
  .footer__partner { white-space: nowrap; margin-bottom: 3px; }
  .sheet--blank .footer { left: 25px; width: 432px; top: 632px; text-align: center; }
  .sheet--letter .footer { left: 35px; width: 415px; top: 625px; text-align: left; }
</style>
</head>
<body>
<div class="canvas">

  <section class="sheet sheet--blank">
    <div class="wordmark">
      <span class="wordmark__name">Pell &amp; Varnum</span>
      <span class="wordmark__tagline">Attorneys At Law, LLP</span>
    </div>
    <div class="star-area" role="img" aria-label="Faint Texas star watermark"></div>
    <footer class="footer">
      <div class="footer__address">1420 E. Lancaster Ave., Fort Worth, TX 76102. <strong>Phone:</strong> (817) 555-0142 <strong>Fax:</strong> (817) 555-0178</div>
      <div class="footer__rule"></div>
      <div class="footer__partner"><strong>NATHAN PELL - Managing Partner</strong> ( Licensed in State of Texas, United States District Court (Northern District of Texas), United States Supreme Court )</div>
      <div class="footer__partner"><strong>LAURA JEAN VARNUM</strong> ( Licensed in the State of Texas )</div>
    </footer>
  </section>

  <section class="sheet sheet--letter">
    <div class="wordmark">
      <span class="wordmark__name">Pell &amp; Varnum</span>
      <span class="wordmark__tagline">Attorneys At Law, LLP</span>
    </div>
    <div class="letter-body">
      <div class="letter-body__salutation">Dear sir / madame,</div>
      <p>Lorem ipsum dolor sit amet, consectetur adipisicing elit, sed do eiusmod tempor incididunt ut labore et dolore magna aliqua. Ut enim ad minim veniam, quis nostrud exercitation ullamco laboris nisi ut aliquip ex ea commodo consequat. Duis aute irure dolor in reprehenderit in voluptate velit esse cillum dolore eu fugiat nulla pariatur. Excepteur sint occaecat cupidatat non proident, sunt in culpa qui officia deserunt mollit anim id est laborum. Lorem ipsum dolor sit amet, consectetur adipisicing elit, sed do eiusmod tempor incididunt ut labore et dolore magna aliqua. Ut enim ad minim veniam, quis nostrud exercitation ullamco laboris nisi ut aliquip ex ea commodo consequat. Duis aute irure dolor in reprehenderit in voluptate velit esse cillum dolore eu fugiat nulla pariatur. Excepteur sint occaecat cupidatat non proident, sunt in culpa qui officia deserunt mollit anim id est laborum.</p>
      <p>Lorem ipsum dolor sit amet, consectetur adipisicing elit, sed do eiusmod tempor incididunt ut labore et dolore magna aliqua. Ut enim ad minim veniam, quis nostrud exercitation ullamco laboris nisi ut aliquip ex ea commodo consequat. Duis aute irure dolor in reprehenderit in voluptate velit esse cillum dolore eu fugiat nulla pariatur. Excepteur sint occaecat cupidatat non proident, sunt in culpa qui officia deserunt mollit anim id est laborum.</p>
      <p>Lorem ipsum dolor sit amet, consectetur adipisicing elit, sed do eiusmod tempor incididunt ut labore et dolore magna aliqua. Ut enim ad minim veniam, quis nostrud exercitation ullamco laboris nisi ut aliquip ex ea commodo consequat. Duis aute irure dolor in reprehenderit in voluptate velit esse cillum dolore eu fugiat nulla pariatur. Excepteur sint occaecat cupidatat non proident, sunt in culpa qui officia deserunt mollit anim id est laborum.</p>
      <p>Lorem ipsum dolor sit amet, consectetur adipisicing elit, sed do eiusmod tempor incididunt ut labore et dolore magna aliqua. Ut enim ad minim veniam, quis nostrud exercitation ullamco laboris nisi ut aliquip ex ea commodo consequat. Duis aute irure dolor in reprehenderit in voluptate velit esse cillum dolore eu fugiat nulla pariatur. Excepteur sint occaecat cupidatat non proident, sunt in culpa qui officia deserunt mollit anim id est laborum.</p>
    </div>
    <div class="signature-area" role="img" aria-label="Handwritten signature"></div>
    <div class="closing">
      <div class="closing__phrase">Yours Sincerely,</div>
      <div class="closing__name">Dana Whitlow</div>
    </div>
    <footer class="footer">
      <div class="footer__address">1420 E. Lancaster Ave., Fort Worth, TX 76102. <strong>Phone:</strong> (817) 555-0142 <strong>Fax:</strong> (817) 555-0178</div>
      <div class="footer__rule"></div>
      <div class="footer__partner"><strong>NATHAN PELL - Managing Partner</strong> ( Licensed in State of Texas, United States District Court (Northern District of Texas), United States Supreme Court )</div>
      <div class="footer__partner"><strong>LAURA JEAN VARNUM</strong> ( Licensed in the State of Texas )</div>
    </footer>
    <div class="sheet__band"></div>
  </section>

</div>
</body>
</html>
```